White Paper and One-Page Advertisement for TELVORISH-QM

I need both documents to be better formatted and designed so they look professional, not something someone with mediocre word skills put together. They will go out to 1000s of industry professionals, and they need to look sharp. I need them to have my company's color palate logo, and branding on it similar to how it is now, but better. Please do not change any of the written content, but it can be arranged in any other format you think is better. Smart art and things i've already used can be omitted in favor of better designs. The developer is free to use their creativity. White paper should not be longer than the three pages unless necessary.

Target Market(s)

Life Sciences supply chain professionals

Colors
33b8a4
0592cd
9bcb3c
fbee3e
3277b5

Requirements
Must have
• Must be professional looking and not look like something done in word. Please use the color palate as seen on the documents.
Should not have
• Any changes to the written content.

```html
<!DOCTYPE html>
<html lang="en">
<head>
<meta charset="utf-8">
<title>Changing Pharma's Paradigm of Waste — TELVORISH-QM</title>
<link rel="stylesheet" href="https://fonts.googleapis.com/css2?family=Montserrat:wght@300;400;700&display=swap">
<style>
  :root {
    --teal: #33b8a4;
    --blue: #0592cd;
    --green: #9bcb3c;
    --deep-teal: #1f8a78;
    --ink-grey: #555a5e;
    --paper: #ffffff;
  }
  * { margin: 0; padding: 0; box-sizing: border-box; }
  html, body { width: 927px; height: 1200px; overflow: hidden; background: var(--paper); }
  .cover {
    position: relative;
    width: 927px;
    height: 1200px;
    overflow: hidden;
    font-family: "Montserrat", sans-serif;
    background: var(--paper);
  }
  .backdrop { position: absolute; inset: 0; width: 927px; height: 1200px; }
  .brand {
    position: absolute;
    left: 594px;
    top: 150px;
    display: flex;
    align-items: center;
    gap: 10px;
  }
  .brand-dot {
    width: 18px; height: 18px;
    border-radius: 50%;
    background: var(--deep-teal);
  }
  .brand-name {
    font-weight: 700;
    font-size: 24px;
    letter-spacing: 1px;
    color: var(--deep-teal);
  }
  .portraits { position: absolute; inset: 0; width: 927px; height: 1200px; }
  .title {
    position: absolute;
    left: 572px;
    top: 662px;
    font-weight: 700;
    font-size: 44px;
    line-height: 52px;
    letter-spacing: 1.5px;
    white-space: nowrap;
    background: linear-gradient(90deg, var(--blue) 0%, var(--teal) 45%, var(--green) 100%);
    -webkit-background-clip: text;
    background-clip: text;
    color: transparent;
  }
  .subtitle {
    position: absolute;
    left: 572px;
    top: 893px;
    font-weight: 400;
    font-size: 18px;
    line-height: 25px;
    white-space: nowrap;
    color: var(--ink-grey);
  }
  .byline {
    position: absolute;
    left: 572px;
    top: 1020px;
    display: flex;
    gap: 18px;
    font-size: 40px;
    line-height: 36px;
  }
  .date .month { display: block; font-weight: 700; color: var(--teal); }
  .date .year { display: block; font-weight: 400; color: var(--teal); }
  .author { font-weight: 300; color: var(--ink-grey); }
  .author span { display: block; }
</style>
</head>
<body>
<main class="cover">
  <svg class="backdrop" viewBox="0 0 927 1200" aria-hidden="true">
    <g class="corner-arcs-top">
      <circle cx="0" cy="0" r="330" fill="#9bcb3c" opacity="0.14"/>
      <circle cx="0" cy="0" r="230" fill="#33b8a4" opacity="0.14"/>
      <circle cx="0" cy="0" r="130" fill="#33b8a4" opacity="0.16"/>
    </g>
    <g class="corner-arcs-bottom">
      <circle cx="0" cy="1200" r="520" fill="#33b8a4" opacity="0.10"/>
      <circle cx="0" cy="1200" r="400" fill="#9bcb3c" opacity="0.12"/>
      <circle cx="0" cy="1200" r="280" fill="#33b8a4" opacity="0.14"/>
      <circle cx="0" cy="1200" r="160" fill="#0592cd" opacity="0.10"/>
    </g>
    <rect x="0" y="0" width="8" height="1200" fill="#33b8a4" opacity="0.5"/>
  </svg>

  <div class="brand">
    <span class="brand-dot"></span>
    <span class="brand-name">TELVORISH-QM</span>
  </div>

  <svg class="portraits" viewBox="0 0 927 1200">
    <defs>
      <linearGradient id="ring" x1="0" y1="0" x2="1" y2="1">
        <stop offset="0" stop-color="#9bcb3c"/>
        <stop offset="1" stop-color="#0592cd"/>
      </linearGradient>
      <radialGradient id="photoChild" cx="0.5" cy="0.45" r="0.6">
        <stop offset="0" stop-color="#d9c3b2"/>
        <stop offset="1" stop-color="#9c948b"/>
      </radialGradient>
      <radialGradient id="photoWoman" cx="0.55" cy="0.45" r="0.6">
        <stop offset="0" stop-color="#8a6248"/>
        <stop offset="1" stop-color="#4c4a3a"/>
      </radialGradient>
      <radialGradient id="photoElder" cx="0.45" cy="0.45" r="0.65">
        <stop offset="0" stop-color="#e6d2c4"/>
        <stop offset="0.6" stop-color="#c9a24a"/>
        <stop offset="1" stop-color="#3a5aa8"/>
      </radialGradient>
    </defs>

    <g class="portrait portrait-child">
      <circle cx="294" cy="324" r="136" fill="url(#photoChild)" role="img" aria-label="Photo of a young child in a knitted hooded sweater"/>
      <circle cx="294" cy="324" r="137" fill="none" stroke="url(#ring)" stroke-width="2.5"/>
    </g>

    <g class="portrait portrait-woman">
      <circle cx="592" cy="440" r="172" fill="url(#photoWoman)" role="img" aria-label="Photo of a young woman in profile wearing a drop earring"/>
      <circle cx="592" cy="440" r="173" fill="none" stroke="url(#ring)" stroke-width="2.5"/>
    </g>

    <g class="portrait portrait-elder">
      <circle cx="310" cy="656" r="204" fill="url(#photoElder)" role="img" aria-label="Photo of a smiling elderly woman with white hair and glasses"/>
      <circle cx="310" cy="656" r="205" fill="none" stroke="url(#ring)" stroke-width="2.5"/>
    </g>
  </svg>

  <h1 class="title">CHANGING<br>PHARMA'S<br>PARADIGM<br>OF WASTE</h1>

  <p class="subtitle">How Pharma's Demand<br>Volatility Could Be Costing<br>You Millions in Material<br>Write-downs &amp; Procurement</p>

  <div class="byline">
    <div class="date"><span class="month">AUG</span><span class="year">2018</span></div>
    <div class="author"><span>Dale</span><span>Morrow</span></div>
  </div>
</main>
</body>
</html>
```